Veranix - Solution provider in business consulting

Veranix is a swiss based company providing solutions for developing markets. The business covers various fields of business consulting, such as supply chain, product costs, quality management and manufacturing management. The Business operates in a efficient, straight and solution oriented manner.
The final design should communicate these characteristics. Asian people as well as as western people shall identify the qualities of the company at first sight.
The customer needs business cards with a simple view but an recognizable design, printed in high quality. Engraved elements such as the globe or simple words are possible.
Available colors are: (RAL)
102/102/102
51/102/102
153/204/153
255/102/51
Font: Calibri

```html
<!DOCTYPE html>
<html lang="en">
<head>
<meta charset="utf-8">
<title>Veranix – Business Card</title>
<link href="https://fonts.googleapis.com/css2?family=Carlito:wght@400;700&display=swap" rel="stylesheet">
<style>
  :root {
    --page-bg: #e9e7e3;
    --card-dark: #5e5e5e;
    --card-mid: #707070;
    --card-light: #7c7c7c;
    --ink-white: #f4f4f4;
    --ink-soft: #e2e2e2;
    --paper-white: #f7f7f7;
  }
  * { margin: 0; padding: 0; box-sizing: border-box; }
  html, body {
    width: 1200px; height: 1022px; overflow: hidden;
    background: var(--page-bg);
    font-family: "Carlito", Calibri, sans-serif;
  }
  .stage {
    width: 1200px; height: 1022px;
    display: flex; align-items: center; justify-content: center;
  }
  .business-card {
    position: relative;
    width: 900px; height: 540px;
    border-radius: 22px;
    overflow: hidden;
    background: linear-gradient(160deg, var(--card-light) 0%, var(--card-mid) 45%, var(--card-dark) 100%);
    box-shadow: 0 12px 30px rgba(0,0,0,.25);
    color: var(--ink-white);
  }
  .accent-shape { position: absolute; inset: 0; }
  .wordmark {
    position: absolute; left: 70px; top: 105px;
    font-size: 92px; font-weight: 400; letter-spacing: 1px;
    color: var(--ink-white); line-height: 1;
  }
  .contact-block { position: absolute; left: 150px; top: 250px; }
  .person-name { font-size: 32px; font-weight: 700; line-height: 1.1; }
  .person-role, .address-line { font-size: 20px; color: var(--ink-soft); line-height: 1.3; }
  .person-role { margin-bottom: 4px; }
  .contact-divider { width: 270px; height: 1px; background: var(--ink-soft); margin: 10px 0 8px; }
  .contact-list { list-style: none; }
  .contact-list li {
    display: flex; align-items: center; gap: 12px;
    font-size: 20px; color: var(--ink-soft); line-height: 1.35;
  }
  .contact-list svg { width: 16px; height: 16px; flex: none; }
</style>
</head>
<body>
<main class="stage">
  <article class="business-card">
    <svg class="accent-shape" viewBox="0 0 900 540">
      <circle cx="830" cy="170" r="150" fill="var(--paper-white)" role="img" aria-label="Globe illustration area"/>
      <line x1="430" y1="320" x2="830" y2="320" stroke="var(--ink-soft)" stroke-width="1.5"/>
    </svg>

    <div class="wordmark">veranix</div>

    <section class="contact-block">
      <h1 class="person-name">Marco Feller</h1>
      <p class="person-role">CEO</p>
      <p class="address-line">Veranix GmbH Talweg 14</p>
      <p class="address-line">9240 Uzwil Switzerland</p>
      <div class="contact-divider"></div>
      <ul class="contact-list">
        <li>
          <svg viewBox="0 0 16 16" aria-hidden="true"><rect x="4" y="1" width="8" height="14" rx="1.5" fill="none" stroke="currentColor" stroke-width="1.5"/></svg>
          +41 79 555 0142
        </li>
        <li>
          <svg viewBox="0 0 16 16" aria-hidden="true"><path d="M4 1 L6.5 4 L5 6 Q7 10 10 11 L12 9.5 L15 12 L13 15 Q4 13 1 3 Z" fill="currentColor"/></svg>
          +41 71 555 0187
        </li>
        <li>
          <svg viewBox="0 0 16 16" aria-hidden="true"><rect x="1" y="3" width="14" height="10" fill="none" stroke="currentColor" stroke-width="1.5"/><path d="M1 3 L8 9 L15 3" fill="none" stroke="currentColor" stroke-width="1.5"/></svg>
          marco.feller@veranix.ch
        </li>
        <li>
          <svg viewBox="0 0 16 16" aria-hidden="true"><circle cx="8" cy="8" r="6.5" fill="none" stroke="currentColor" stroke-width="1.5"/><line x1="1.5" y1="8" x2="14.5" y2="8" stroke="currentColor" stroke-width="1.2"/><ellipse cx="8" cy="8" rx="3" ry="6.5" fill="none" stroke="currentColor" stroke-width="1.2"/></svg>
          www.veranix.ch
        </li>
      </ul>
    </section>
  </article>
</main>
</body>
</html>
```